Veltrane Group Business Card Design

The CEO is looking for a new trendy look for his business card.
You can stay with current branding or come up with something new/creative. It can be 3D, including Medical Office buildings. You can use our logo in a variety of colors. Please include name, title, company name, company website, email address, cell number

Target Market(s)

Real Estate Development and Construction

Industry/Entity Type

Health care real estate

Contact Information for Business Card

Rohesh Kamdar, CEO M-604.781.2249 E-roheshkamdar@veltrane.com Address:4180 Lindqvist Ave, Tampa, FL 33482 www.veltrane.com

Font styles to use
Other font styles liked:
• Be creative

Requirements
Must have
• Creative, trendy look
Nice to have
• Please go to our website to get a feel- www. veltrane.com
Should not have
• small fonts

```html
<!DOCTYPE html>
<html lang="en">
<head>
<meta charset="utf-8">
<title>Veltrane Group Business Card</title>
<link href="https://fonts.googleapis.com/css2?family=Poppins:wght@400;500;700;800&display=swap" rel="stylesheet">
<style>
  :root {
    --bg: #c4c4c4;
    --brand-red: #b01f2a;
    --brand-red-light: #d42a38;
    --navy: #1c2a4d;
    --ink: #2a2a2a;
    --paper: #ffffff;
    --rule: #9a9a9a;
  }
  * { box-sizing: border-box; margin: 0; padding: 0; }
  html, body {
    width: 1200px; height: 1015px; overflow: hidden;
    background: var(--bg);
    font-family: "Poppins", sans-serif;
  }
  .sheet {
    position: relative; width: 1200px; height: 1015px;
    display: flex; flex-direction: column; align-items: center; justify-content: center; gap: 60px;
  }
  .card {
    position: relative; width: 620px; height: 354px;
    box-shadow: 0 10px 24px rgba(0,0,0,.28);
  }
  .card-front { background: var(--brand-red); }
  .card-back { background: var(--paper); }
  .card-frame {
    position: absolute; inset: 24px;
    border: 1px solid var(--paper);
  }
  .card-back .card-frame { border-color: var(--brand-red); }

  .front-name {
    position: absolute; inset: 0;
    display: flex; align-items: center; justify-content: center;
    font-weight: 800; font-size: 64px; letter-spacing: -1px;
    color: var(--brand-red-light);
  }

  .back-brand {
    position: absolute; left: 70px; top: 0; bottom: 0; width: 230px;
    display: flex; align-items: center;
    font-weight: 800; font-size: 44px; letter-spacing: -1px; line-height: 1;
    color: var(--brand-red);
  }
  .back-divider {
    position: absolute; left: 318px; top: 90px; height: 170px;
    border-left: 1px solid var(--rule);
  }
  .contact {
    position: absolute; left: 340px; top: 88px; right: 30px;
    color: var(--ink);
  }
  .contact-name { font-weight: 700; font-size: 21px; color: var(--brand-red); line-height: 1.1; }
  .contact-title { font-weight: 500; font-size: 14px; color: var(--navy); margin-bottom: 12px; }
  .contact-list { list-style: none; font-size: 13px; line-height: 1.6; }
  .contact-list li { display: flex; align-items: center; gap: 7px; }
  .contact-list svg { width: 12px; height: 12px; fill: var(--brand-red); flex: none; }
  .contact-address { font-size: 13px; line-height: 1.35; margin-top: 10px; padding-left: 19px; }
</style>
</head>
<body>
<main class="sheet">
  <section class="card card-front" aria-label="Card front">
    <div class="card-frame"></div>
    <div class="front-name">Veltrane Group</div>
  </section>

  <section class="card card-back" aria-label="Card back">
    <div class="card-frame"></div>
    <div class="back-brand">Veltrane Group</div>
    <div class="back-divider"></div>
    <div class="contact">
      <p class="contact-name">Rohesh Kamdar</p>
      <p class="contact-title">CEO</p>
      <ul class="contact-list">
        <li><svg viewBox="0 0 24 24"><path d="M6.6 10.8a15.1 15.1 0 0 0 6.6 6.6l2.2-2.2a1 1 0 0 1 1-.25 11.4 11.4 0 0 0 3.6.57 1 1 0 0 1 1 1V20a1 1 0 0 1-1 1A17 17 0 0 1 3 4a1 1 0 0 1 1-1h3.5a1 1 0 0 1 1 1c0 1.25.2 2.45.57 3.57a1 1 0 0 1-.25 1z"/></svg>604.781.2249</li>
        <li><svg viewBox="0 0 24 24"><path d="M2 5h20v14H2zm2 2v.4l8 5.1 8-5.1V7z"/></svg>roheshkamdar@veltrane.com</li>
        <li><svg viewBox="0 0 24 24"><path d="M12 2a10 10 0 1 0 0 20 10 10 0 0 0 0-20zm6.9 9h-3a15 15 0 0 0-1.3-6A8 8 0 0 1 18.9 11zM12 4.1c.9 1.2 1.7 3.6 1.9 6.9h-3.8c.2-3.3 1-5.7 1.9-6.9zM9.4 5A15 15 0 0 0 8.1 11h-3A8 8 0 0 1 9.4 5zM5.1 13h3a15 15 0 0 0 1.3 6A8 8 0 0 1 5.1 13zm6.9 6.9c-.9-1.2-1.7-3.6-1.9-6.9h3.8c-.2 3.3-1 5.7-1.9 6.9zm2.6-.9a15 15 0 0 0 1.3-6h3a8 8 0 0 1-4.3 6z"/></svg>www.veltrane.com</li>
      </ul>
      <p class="contact-address">4180 Lindqvist Ave, Tampa<br>FL 33482</p>
    </div>
  </section>
</main>
</body>
</html>
```